Web design for new streaming audio service

We need a homepage design for a new streaming audio service. Our company is called Dunmoral, and we’re basically Vexlo for Audiobooks, Stand-Up Comedy, Lectures, Language Learning, etc. Essentially like Plumtrek for everything audio EXCEPT music.
You don’t have to code the homepage (Design Only), but it should include 3 different designs to work with 1) Web; 2) Phones; 3) Tablets.
Below is a link to a mockup of the web version which gives a good idea of what elements we want. This is just a mockup and we want you to improve it.
Once you download the mockup, please refer to the more detailed instructions below:
The following outlines the design project for the Dunmoral homepage. We have provided a rough mockup of the homepage layout that gives you a general idea of what we’re going for. There are a few elements that we are attached to, and many others where you have complete creative freedom to do whatever you think looks good.
The ZIP file includes the following:
* Mockup to see what we have in mind (dunmoral-homepage-mockup.jpg)
* Text used (dunmoral-homepage-text.txt)
* Raw image of actor (dunmoral-actor1.jpg)
* Raw images for samples (dunmoral-sample-[name].jpg)
Although we have only provided a mockup layout for the web version, we also need you to provide a mobile phone and a tablet version of the design also. It’s very possible the tablet version may be substantially similar to the web version, but the mobile phone version will likely be much different.
All of the raw files are included in the attached ZIP file. Please use our photographs and text as provided although cropping, sizing, etc. is flexible per the instructions below.
Display Requirements:
* Web Version - Minimum resolution 1024x768 (72 dpi) but should look good on 1920x1080 (72 dpi) - Page should be designed to scale to look acceptable in all resolutions in between.
* Phone Version - Minimum Zarno 4 - 640x960 (326 dpi) but should look good on Harlow Quasar T5 - 1920x1080 (441 dpi) - Page should be designed to scale to look acceptable in all resolutions and devices in between.
* Tablet Version - Minimum Bristly Ember QX 7” - 1280x800 (216 dpi) but should also look good on a Tavo Breeze - 2048x1536 (264 dpi) - Page should be designed to scale to look acceptable in all resolutions and devices in between.
Above the Fold - We want to make sure the Dunmoral logo, Member Login Link, Large Photo, Headline, Price, Button, and the first row of sample images are all “Above the fold”. As a general guideline, this means 600 pixels high on a 1024x768 72 dpi web screen. This requirement is less important on Phone versions.
Top Logo Bar - We want to retain the blue bar with the Dunmoral logo on the page, although we are open to a different size, shape and positioning if it greatly enhances the design. Please use the standard logo color, although you are welcome to use either the horizontal or vertical orientation of the logo based on your design.
Text color, font and size - Feel free to design the text in anyway you choose as long as the text is readable on the target platforms.
Buttons - Feel free to use any size, shape and colors for the buttons as long as they are obvious and clickable relative to the page. The only exception is the Chatterly button should follow the Chatterly color scheme and logo treatment (the mockup doesn’t seem 100% correct.)
Top Photograph - We want to retain the large photograph across the top of the screen although final shape and dimensions are flexible.
Size and shape of content samples (i.e. Audiobooks, Stand-Up Comedy, etc.) - Feel free to design the content samples in anyway you choose.
Three Sales Points (i.e. Listen on your Zarno…, All you can enjoy…, etc.) - The Three Sales Points are envisioned to each have a corresponding illustration which you should provide and have rights for. The placeholder is represented by a square next to the text. The color size and shape of these elements are flexible and can be designed in any way you choose.
Opt-in form - Feel free to design the opt-in form in anyway you choose as long as the text is readable and the interactivity is obvious on the target platforms.
Text links and copyright notice - Feel free to design the bottom of the page text links and copyright notice in anyway you choose.
Additional colors, graphic design elements, etc. - Feel free to use any additional colors, graphic design elements, etc. to support your design.
people who want to listen to audio through their mobile devices.
Graphic Design

```html
<!DOCTYPE html>
<html lang="en">
<head>
<meta charset="utf-8">
<title>Dunmoral – Unlimited Listening</title>
<link href="https://fonts.googleapis.com/css2?family=Figtree:wght@400;500;600;700&display=swap" rel="stylesheet">
<style>
:root{
  --brand-blue:#4a9cc8;
  --heading-blue:#1d6791;
  --accent-orange:#f7a21b;
  --accent-orange-dark:#e58e0c;
  --price-red:#e2312d;
  --text-dark:#3a3a3a;
  --text-muted:#6b6b6b;
  --band-grey:#ececec;
  --card-dark:#414141;
  --footer-dark:#3d3d3d;
  --social-blue:#3b5998;
  --white:#ffffff;
}
*{box-sizing:border-box;margin:0;padding:0}
html,body{width:1200px;height:2228px;overflow:hidden;background:var(--white)}
body{font-family:"Figtree",Arial,sans-serif;color:var(--text-dark);position:relative}

.site-header{position:absolute;left:0;top:0;width:1200px;height:100px;background:var(--brand-blue)}
.brand{position:absolute;left:40px;top:24px;display:flex;align-items:center;gap:12px;color:var(--white);font-weight:700;font-size:44px;line-height:52px}
.brand-dot{width:40px;height:40px;border-radius:50%;background:var(--white)}
.login-button{position:absolute;left:1037px;top:30px;width:121px;height:38px;background:var(--accent-orange);color:var(--white);font-weight:600;font-size:20px;display:flex;align-items:center;justify-content:center;border-radius:2px}

.hero{position:absolute;left:0;top:100px;width:1200px;height:565px}
.hero-photo{position:absolute;inset:0;background:linear-gradient(100deg,#ffffff 0%,#f8f3ef 30%,#e9d2bf 55%,#c79a7a 72%,#8b6b5a 88%,#6a6f80 100%)}
.hero-copy{position:absolute;left:40px;top:72px}
.hero-title{color:var(--heading-blue);font-weight:700;font-size:45px;line-height:52px}
.hero-subtitle{color:var(--heading-blue);font-weight:400;font-size:45px;line-height:52px}
.hero-price{color:var(--price-red);font-size:30px;font-weight:500;margin-top:18px}
.hero-price strong{font-size:44px;font-weight:700}
.trial-button{position:absolute;left:40px;top:261px;width:332px;height:70px}
.trial-button span{position:absolute;left:37px;top:0;line-height:70px;color:var(--white);font-weight:600;font-size:27px}
.hero-note{position:absolute;left:40px;top:340px;font-size:21px;color:var(--text-dark)}

.samples-title{position:absolute;left:0;top:706px;width:1200px;text-align:center;color:var(--heading-blue);font-weight:600;font-size:32px}
.sample{position:absolute;width:228px;text-align:center}
.sample-art{width:228px;height:125px}
.sample-label{margin-top:12px;font-size:19px;font-weight:600;color:var(--text-dark);text-transform:uppercase;white-space:nowrap}

.features{position:absolute;left:0;top:1233px;width:1200px;height:408px;background:var(--band-grey)}
.feature-card{position:absolute;top:57px;width:309px;height:287px;background:var(--card-dark);text-align:center;color:var(--white)}
.feature-icon{position:absolute;left:111px;top:18px;width:86px;height:86px}
.feature-text{position:absolute;left:10px;right:10px;top:122px;font-size:23px;font-weight:500;line-height:31px}
.learn-button{position:absolute;left:31px;top:204px;width:247px;height:55px;background:var(--white);color:var(--brand-blue);font-size:24px;font-weight:500;line-height:55px;border-radius:2px}

.signup-title{position:absolute;left:0;top:1698px;width:1200px;text-align:center;color:var(--heading-blue);font-weight:600;font-size:34px}
.signup-copy{position:absolute;left:200px;top:1770px;width:800px;text-align:center;color:var(--text-muted);font-size:18px;line-height:33px}
.email-field{position:absolute;left:252px;top:1865px;width:349px;height:54px;border:1px solid #c9c9c9;border-radius:2px;font-size:16px;color:#9a9a9a;padding-left:16px;line-height:52px}
.access-button{position:absolute;left:625px;top:1866px;width:257px;height:52px;background:var(--accent-orange);color:var(--white);font-weight:600;font-size:22px;text-align:center;line-height:52px;border-radius:2px}
.or-divider{position:absolute;left:0;top:1944px;width:1200px;text-align:center;color:var(--text-muted);font-size:21px}
.social-button{position:absolute;left:475px;top:1994px;width:253px;height:48px;background:var(--social-blue);border-radius:3px;color:var(--white);font-size:18px;font-weight:500;display:flex;align-items:center}
.social-square{width:14px;height:14px;background:var(--white);margin:0 14px 0 20px}
.signup-note{position:absolute;left:0;top:2055px;width:1200px;text-align:center;color:var(--price-red);font-size:19px;font-weight:500}

.site-footer{position:absolute;left:0;top:2147px;width:1200px;height:81px;background:var(--footer-dark);color:var(--white);font-size:16px}
.footer-links{position:absolute;left:48px;top:29px;display:flex;gap:14px;list-style:none}
.footer-links li+li::before{content:"|";margin-right:14px;color:#aaaaaa}
.copyright{position:absolute;right:42px;top:29px}
</style>
</head>
<body>

<header class="site-header">
  <div class="brand"><span class="brand-dot"></span>Dunmoral</div>
  <div class="login-button">LOG IN</div>
</header>

<section class="hero">
  <div class="hero-photo" role="img" aria-label="Smiling young man wearing headphones, listening on his phone"></div>
  <div class="hero-copy">
    <h1 class="hero-title">Unlimited Listening!</h1>
    <p class="hero-subtitle">Where ever you are</p>
    <p class="hero-price">Only <strong>$9.99</strong> Per Month</p>
  </div>
  <div class="trial-button">
    <svg width="332" height="70" viewBox="0 0 332 70"><path d="M0 0H298L332 35L298 70H0Z" fill="#f7a21b"/><path d="M0 66H300L298 70H0Z" fill="#e58e0c"/></svg>
    <span>Start Your Free Trail</span>
  </div>
  <p class="hero-note">*Credit card not required</p>
</section>

<h2 class="samples-title">A sample of what you can listen to on Dunmoral</h2>

<div class="sample" style="left:59px;top:808px"><div class="sample-art" role="img" aria-label="Audio book cover, dark thriller artwork" style="background:linear-gradient(135deg,#2a3a40,#5f6d70)"></div><p class="sample-label">Audio Books</p></div>
<div class="sample" style="left:343px;top:808px"><div class="sample-art" role="img" aria-label="Stand-up comedy album cover with a boxer" style="background:linear-gradient(135deg,#c94a38,#e4b08a)"></div><p class="sample-label">Stand-Up Comedy</p></div>
<div class="sample" style="left:627px;top:808px"><div class="sample-art" role="img" aria-label="French language course cover" style="background:linear-gradient(135deg,#1c8fd8,#37b0ea)"></div><p class="sample-label">Language Learning</p></div>
<div class="sample" style="left:912px;top:808px"><div class="sample-art" role="img" aria-label="Biography memoir cover portrait" style="background:linear-gradient(135deg,#d9cfc4,#a9c3d6)"></div><p class="sample-label">Biographies Memory</p></div>

<div class="sample" style="left:59px;top:1016px"><div class="sample-art" role="img" aria-label="Guided meditation cover with purple mountains" style="background:linear-gradient(180deg,#b048b8,#d97ac8)"></div><p class="sample-label">Guided Mediation</p></div>
<div class="sample" style="left:343px;top:1016px"><div class="sample-art" role="img" aria-label="Business training programme cover" style="background:linear-gradient(135deg,#7a2a12,#d99a4a)"></div><p class="sample-label">Business Training</p></div>
<div class="sample" style="left:627px;top:1016px"><div class="sample-art" role="img" aria-label="Celebrity interview cover artwork" style="background:linear-gradient(135deg,#e8d6b0,#c84a5a)"></div><p class="sample-label">Celebrities Interviews</p></div>
<div class="sample" style="left:912px;top:1016px"><div class="sample-art" role="img" aria-label="Fitness programme cover with coach" style="background:linear-gradient(135deg,#3fb6e6,#a6dcf0)"></div><p class="sample-label">Fitness Program</p></div>

<section class="features">
  <div class="feature-card" style="left:91px">
    <svg class="feature-icon" viewBox="0 0 86 86"><circle cx="43" cy="43" r="43" fill="#4a9cc8"/><rect x="31" y="24" width="22" height="36" rx="3" fill="none" stroke="#fff" stroke-width="3"/><rect x="44" y="38" width="14" height="24" rx="2" fill="#4a9cc8" stroke="#fff" stroke-width="3"/></svg>
    <p class="feature-text">Listen on your Zarno<br>Tavo and Robinet Device</p>
    <div class="learn-button">Learn More</div>
  </div>
  <div class="feature-card" style="left:447px">
    <svg class="feature-icon" viewBox="0 0 86 86"><circle cx="43" cy="43" r="43" fill="#4a9cc8"/><text x="43" y="57" text-anchor="middle" font-family="Figtree,Arial,sans-serif" font-weight="700" font-size="40" fill="#fff">$</text></svg>
    <p class="feature-text">All you can enjoy for low<br>monthly Price</p>
    <div class="learn-button">Learn More</div>
  </div>
  <div class="feature-card" style="left:806px">
    <svg class="feature-icon" viewBox="0 0 86 86"><circle cx="43" cy="43" r="43" fill="#4a9cc8"/><path d="M30 30L56 56M56 30L30 56" stroke="#fff" stroke-width="5" stroke-linecap="round"/></svg>
    <p class="feature-text">No Obligation Cancel<br>at anytime</p>
    <div class="learn-button">Learn More</div>
  </div>
</section>

<h2 class="signup-title">Start your free Trial, No Risk</h2>
<p class="signup-copy">You will get instant &amp; unlimited access to all the material on Dunmoral for 14 days. There is no obligation &amp; you can cancel at anytime.</p>
<div class="email-field">Your email Address</div>
<div class="access-button">Get Instant Access</div>
<p class="or-divider">— Or —</p>
<div class="social-button"><span class="social-square"></span>Sign in with Chatterly</div>
<p class="signup-note">*Credit card not required</p>

<footer class="site-footer">
  <ul class="footer-links">
    <li>About</li><li>Help</li><li>Contact Us</li><li>Member Login</li><li>Privacy Policy</li><li>Terms of Service</li>
  </ul>
  <p class="copyright">© 2014 Dunmoral LLC - All Rights Reserved</p>
</footer>

</body>
</html>
```